Brightwell Supports

We need an updated website that captures the comprehensive services and supports we provide to persons with developmental disabilities. We need a website design that educates families about the services we provide. We would also need a website that is user-friendly so that we could periodically update training schedules and ongoing programming.

• Thank you for submitting designs.  A few things I am hoping to see offered in the website:
• Front page highlights the services we offer (host homes, family caregiver, day program, employment program, SLS program, supported apartment program, behavior/clinical program)
• Front page also highlights any new programs we want to make prominent:  family caregiver, future restaurant employment openings, etc...
• Interactive Training Calendar
• Employee Resources page (link to carevo, email login, etc.)
• Uniform provider application for host home providers
• Information on agency - history, goals, etc.
• Contact Information/Location

 

Fun things to include:

• Client Highlights (featuring a client story each month, etc...)
• Employee highlights (featuring a staff member...)
• link to other Brightwell business pages (Brightwell Therapy and Brightwell Restaurant)

```html
<!DOCTYPE html>
<html lang="en">
<head>
<meta charset="utf-8">
<title>Brightwell Supports</title>
<link href="https://fonts.googleapis.com/css2?family=Open+Sans:wght@400;600&family=Oxygen:wght@400;700&family=Ubuntu:wght@400&family=Crimson+Text:wght@600&display=swap" rel="stylesheet">
<style>
:root{
  --red:#a3070f;
  --red-dark:#7e050b;
  --red-text:#a8141b;
  --ink:#2b2b2b;
  --body:#555;
  --line:#d8d8d8;
  --band:#f0f0f0;
  --footer-top:#2c2c2c;
  --footer-bottom:#111;
  --footer-text:#e6e6e6;
}
*{box-sizing:border-box;margin:0;padding:0}
html,body{width:954px;height:1200px;overflow:hidden;background:#fff}
body{font-family:"Open Sans",Arial,sans-serif;color:var(--body);position:relative}
.page{position:relative;width:954px;height:1200px;overflow:hidden}
.top-strip{position:absolute;left:0;top:0;width:954px;height:5px;background:#e8e8e8}

/* header */
.brand{position:absolute;left:78px;top:38px;display:flex;align-items:center;gap:8px}
.brand-dot{width:18px;height:18px;border-radius:50%;background:var(--red)}
.brand-name{font-family:"Oxygen",sans-serif;font-weight:700;font-size:21px;color:var(--red-dark);letter-spacing:.2px}
.util-links{position:absolute;right:76px;top:15px;font-size:12px;color:#444;display:flex;gap:8px}
.util-links span.sep{color:#666}
.phone{position:absolute;right:78px;top:62px;display:flex;align-items:center;gap:4px;font-family:"Oxygen",sans-serif;font-size:19px;color:#222}
.phone svg{width:14px;height:16px}

/* nav */
.main-nav{position:absolute;left:0;top:98px;width:954px;height:42px;background:linear-gradient(#b80f17,var(--red-dark))}
.main-nav ul{list-style:none;display:flex;position:absolute;left:89px;top:0;height:42px}
.main-nav li{font-family:"Ubuntu",sans-serif;font-size:13.4px;color:#fff;padding:0 10px;line-height:42px;border-right:1px solid rgba(0,0,0,.25)}
.main-nav li:last-child{border-right:none}

/* hero */
.hero-art{position:absolute;left:560px;top:176px;width:240px;height:282px;background:linear-gradient(135deg,#fff 10%,#bfe6fb 50%,#f3c9cc 90%);z-index:0}
.hero-title{position:absolute;left:77px;top:246px;width:500px;font-family:"Oxygen",sans-serif;font-weight:400;font-size:25.5px;line-height:36px;color:var(--red-text);z-index:1}
.hero-text{position:absolute;left:78px;top:325px;width:420px;font-size:10.3px;line-height:17.5px;color:#555;z-index:1}
.hero-dots{position:absolute;left:78px;top:372px;display:flex;gap:3px}
.hero-dots i{width:9px;height:9px;border-radius:50%;background:#ccc;display:block}
.hero-dots i.on{background:var(--red)}

/* feature cards */
.band{position:absolute;left:0;top:478px;width:954px;height:454px;background:linear-gradient(#fff 0,var(--band) 36px,#fff 38px,#fff 100%)}
.cards{position:absolute;left:74px;top:477px;display:flex;gap:3px}
.card{width:267px;height:164px;position:relative}
.card-photo{height:108px}
.card-1 .card-photo{background:linear-gradient(120deg,#ddd3c8,#3c3b40)}
.card-2 .card-photo{background:linear-gradient(120deg,#e8e2da,#a9a49f)}
.card-3 .card-photo{background:linear-gradient(#1d6fb4,#9fd3ef)}
.card-caption{height:56px;background:var(--red);color:#fff;padding:7px 0 0 19px;position:relative}
.card-caption h3{font-family:"Open Sans",sans-serif;font-weight:400;font-size:16.5px;line-height:22px}
.card-caption p{font-size:10px;line-height:14px}
.card-caption svg{position:absolute;right:15px;top:19px;width:10px;height:18px}

/* welcome */
.welcome{position:absolute;left:75px;top:698px;width:530px}
.welcome h1{font-family:"Oxygen",sans-serif;font-weight:400;font-size:21.5px;color:#222;margin-bottom:8px}
.welcome p{font-size:10.6px;line-height:17.6px;color:#555;margin-left:4px;margin-bottom:7px;width:524px}
.welcome p.small{font-size:10.1px}

.client-supports{position:absolute;left:621px;top:694px;width:243px}
.client-supports h2{font-family:"Oxygen",sans-serif;font-weight:400;font-size:19.5px;color:#222;margin-left:11px;margin-bottom:8px}
.client-supports ul{list-style:none}
.client-supports li{height:23px;border-bottom:1px solid var(--line);font-size:10.4px;font-weight:600;color:var(--red-text);line-height:22px;padding-left:21px;position:relative}
.client-supports li:last-child{border-bottom:none}
.client-supports li::before{content:"";position:absolute;left:12px;top:8px;border-left:4px solid #aaa;border-top:3px solid transparent;border-bottom:3px solid transparent}

/* footer */
.footer-gap{position:absolute;left:0;top:932px;width:954px;height:8px;background:#e9e9e9}
.site-footer{position:absolute;left:0;top:940px;width:954px;height:260px;background:linear-gradient(var(--footer-top),var(--footer-bottom))}
.f-col{position:absolute;top:40px}
.f-col h4{font-family:"Crimson Text",serif;font-weight:600;font-size:15px;letter-spacing:.6px;color:#fff;margin-bottom:4px}
.f-col li{list-style:none;font-size:10.2px;line-height:20.5px;color:var(--footer-text)}
.f-col.contact li{font-weight:600}
.social{display:flex;gap:4px;margin-top:8px;margin-left:3px}
.social i{display:block;width:24px;height:24px;border-radius:50%;background:#fff}
.f-rule{position:absolute;left:96px;top:204px;width:791px;height:1px;background:#3a3a3a}
.copyright{position:absolute;left:92px;top:222px;font-size:10.2px;color:#bbb}
</style>
</head>
<body>
<div class="page">
  <div class="top-strip"></div>

  <header>
    <div class="brand">
      <span class="brand-dot"></span>
      <span class="brand-name">Brightwell Supports</span>
    </div>
    <nav class="util-links">
      <span>Activity Calendar</span><span class="sep">|</span>
      <span>Training Calender</span><span class="sep">|</span>
      <span>Contact us</span><span class="sep">|</span>
      <span>Location</span>
    </nav>
    <div class="phone">
      <svg viewBox="0 0 14 16"><path d="M3 1 L5.5 1 L6.5 5 L4.8 6.3 C5.6 8.6 7 10.3 9 11.3 L10.3 9.6 L13.5 11 L13 14.5 C6.5 14.5 1.5 8.5 1.5 2.5 Z" fill="#999"/></svg>
      <span>555-014-2290</span>
    </div>
  </header>

  <nav class="main-nav">
    <ul>
      <li>Home</li><li>Available Services</li><li>Residential Program</li><li>SLS Program</li><li>Become a Provider</li><li>Employee Resources</li><li>Meet Our Team</li>
    </ul>
  </nav>

  <section class="hero">
    <div class="hero-art" role="img" aria-label="Illustration of a blue rising arrow held up by stacked red figures"></div>
    <h2 class="hero-title">Building Abilities ~ Creating Opportunities ~ Developing Relationships</h2>
    <p class="hero-text">Auris nunc quam venenatis nec euismod sit amet egesta placerat est Pellentesque habitant morbi tristique senectus et netus et malesuada</p>
    <div class="hero-dots"><i class="on"></i><i></i><i></i><i></i></div>
  </section>

  <div class="band"></div>
  <section class="cards">
    <article class="card card-1">
      <div class="card-photo" role="img" aria-label="Photo of colleagues talking around a table"></div>
      <div class="card-caption">
        <h3>Community Integration</h3>
        <p>Aliquam nec erat at purus cursus interdum</p>
        <svg viewBox="0 0 10 18"><path d="M1 1 L9 9 L1 17" stroke="#fff" stroke-width="1.6" fill="none"/></svg>
      </div>
    </article>
    <article class="card card-2">
      <div class="card-photo" role="img" aria-label="Photo of a team gathered around a laptop"></div>
      <div class="card-caption">
        <h3>Carevoeutic Attachment:</h3>
        <p>Aliquam nec erat at purus cursus interdum</p>
        <svg viewBox="0 0 10 18"><path d="M1 1 L9 9 L1 17" stroke="#fff" stroke-width="1.6" fill="none"/></svg>
      </div>
    </article>
    <article class="card card-3">
      <div class="card-photo" role="img" aria-label="Photo of a businessman leaping against a blue sky"></div>
      <div class="card-caption">
        <h3>Positive Boundaries:</h3>
        <p>Aliquam nec erat at purus cursus interdum</p>
        <svg viewBox="0 0 10 18"><path d="M1 1 L9 9 L1 17" stroke="#fff" stroke-width="1.6" fill="none"/></svg>
      </div>
    </article>
  </section>

  <section class="welcome">
    <h1>Welcome to Brightwell Supports Website</h1>
    <p>Brightwell Supports is an agency designed to creatively serve individuals with developmental disabilities in community-based settings throughout Colorado.&nbsp; Brightwell Supports is an approved service agency through the Division of Developmental Disabilities.</p>
    <p class="small">Pellentesque faucibus Ut accumsan ultricies elit Maecenas at justo id velit placerat molestie Donec dictum lectus non odio Cras a ante vitae enim iaculis aliquam Mauris nunc quam venenatis nec euismod sit amet egesta placerat est Pellentesque habitant morbi tristique senectus et netus et malesuada fames ac turpis egestas Cras id elit Integer quis urna Ut ante enim dapibus malesuada fringilla eu condimentum quis tellus Aenean porttitor eros vel dolor Donec convallis pede venenatis nibh</p>
  </section>

  <aside class="client-supports">
    <h2>Client Supports:</h2>
    <ul>
      <li>Client Advisory Board</li>
      <li>Recreational Support</li>
      <li>Integrated Treatment Plans</li>
      <li>Personal Goal Plans</li>
      <li>Trained Providers</li>
      <li>On-site classes</li>
      <li>Social Networking Club</li>
    </ul>
  </aside>

  <div class="footer-gap"></div>
  <footer class="site-footer">
    <div class="f-col" style="left:97px">
      <h4>COMPANY</h4>
      <ul><li>Welcome</li><li>Available Services</li><li>Residential Program</li><li>Day/Employment Program</li><li>SLS Program</li></ul>
    </div>
    <div class="f-col" style="left:276px">
      <h4>ABOUT</h4>
      <ul><li>Become a Provider</li><li>Employee Resources</li><li>Meet Our Team!</li><li>Activity Calendar</li></ul>
    </div>
    <div class="f-col" style="left:430px">
      <h4>SUPPORT</h4>
      <ul><li>Training Calendar</li><li>Contact Us</li><li>Location</li><li>Community Resource</li></ul>
    </div>
    <div class="f-col contact" style="left:579px">
      <h4>CONTACT</h4>
      <ul><li>418 Alder Row</li><li>Fairhaven, CO 80999</li><li>Phone: 555-014-2290</li><li>Fax: 555-014-7731</li></ul>
    </div>
    <div class="f-col" style="left:730px">
      <h4>GET IN TOUCH</h4>
      <div class="social">
        <i aria-label="Social link"></i><i aria-label="Social link"></i><i aria-label="Social link"></i><i aria-label="Social link"></i>
      </div>
    </div>
    <div class="f-rule"></div>
    <p class="copyright">Copyright ©&nbsp; 2014 Company Name. All rights reserved.</p>
  </footer>
</div>
</body>
</html>
```